Real Estate Card Design

I need a new business card! Below you will find my headshot, the company logo and a copy of my previous business card.

The card must contain the following information:

Dana Wexley
Sales Representative
ALDERWICK REALTY INC BROKERAGE
204-517 Marsh Rd E, Oshawa ON L1H 4K7
Cell: 905-618-3074 Office:905-481-2696
www.danawexley.example dana@homesbywexley.example

I would like the card to portray security and class all the while being fresh and contemporary. I hold the key....

```html
<!DOCTYPE html>
<html lang="en">
<head>
<meta charset="utf-8">
<title>Dana Wexley – Business Card</title>
<link rel="stylesheet" href="https://fonts.googleapis.com/css2?family=Noto+Serif:wght@400&family=Roboto:wght@400&display=swap">
<style>
  :root {
    --page-bg: #ece7e2;
    --card-bg: #ffffff;
    --ink: #1d1d1d;
    --ink-soft: #4a4a4a;
    --accent: #1ba3e8;
    --suit-navy: #141a26;
    --hair-blond: #cdb48c;
  }
  * { box-sizing: border-box; margin: 0; padding: 0; }
  html, body {
    width: 1200px;
    height: 989px;
    overflow: hidden;
    background: var(--page-bg);
  }
  .card {
    position: absolute;
    left: 50px;
    top: 178px;
    width: 1100px;
    height: 634px;
    background: var(--card-bg);
    box-shadow: 0 10px 28px rgba(0,0,0,0.25);
    overflow: hidden;
  }
  .brand {
    position: absolute;
    left: 63px;
    top: 150px;
    width: 340px;
    font-family: "Noto Serif", serif;
    font-weight: 400;
    font-size: 24px;
    line-height: 30px;
    letter-spacing: 0.5px;
    color: var(--ink);
  }
  .agent {
    position: absolute;
    left: 63px;
    top: 258px;
    font-family: "Noto Serif", serif;
    color: var(--ink);
  }
  .agent-name { font-size: 38px; line-height: 46px; font-weight: 400; }
  .agent-title { font-size: 25px; line-height: 30px; }
  .address {
    position: absolute;
    left: 65px;
    top: 356px;
    font-family: "Roboto", sans-serif;
    font-style: normal;
    font-size: 25px;
    line-height: 34px;
    color: var(--ink-soft);
  }
  .contacts {
    position: absolute;
    left: 65px;
    top: 440px;
    list-style: none;
    font-family: "Roboto", sans-serif;
    font-size: 25px;
    color: var(--ink-soft);
  }
  .contacts li {
    display: flex;
    align-items: center;
    height: 35.5px;
  }
  .contacts svg {
    width: 26px;
    height: 26px;
    margin-right: 16px;
    fill: var(--accent);
    flex: none;
  }
  .portrait {
    position: absolute;
    left: 618px;
    top: 25px;
    right: 0;
    bottom: 0;
    border-radius: 200px 200px 0 60px;
    background: linear-gradient(180deg, var(--hair-blond) 0%, #8a7b6c 22%, #3a3f4c 42%, var(--suit-navy) 70%);
  }
</style>
</head>
<body>
  <main class="card">
    <p class="brand">ALDERWICK REALTY INC.<br>BROKERAGE</p>

    <div class="agent">
      <h1 class="agent-name">Dana Wexley</h1>
      <p class="agent-title">Sales Representative</p>
    </div>

    <address class="address">
      204-517 Marsh Rd E,<br>Oshawa ON L1H 4K7
    </address>

    <ul class="contacts">
      <li>
        <svg viewBox="0 0 24 24" aria-hidden="true"><path d="M6.6 10.8a15.1 15.1 0 0 0 6.6 6.6l2.2-2.2c.3-.3.7-.4 1-.2 1.1.4 2.3.6 3.6.6.6 0 1 .4 1 1V20c0 .6-.4 1-1 1A17 17 0 0 1 3 4c0-.6.4-1 1-1h3.5c.6 0 1 .4 1 1 0 1.2.2 2.4.6 3.6.1.3 0 .7-.2 1z"/></svg>
        905-481-2696
      </li>
      <li>
        <svg viewBox="0 0 24 24" aria-hidden="true"><path d="M7 1h10a2 2 0 0 1 2 2v18a2 2 0 0 1-2 2H7a2 2 0 0 1-2-2V3a2 2 0 0 1 2-2zm0 3v14h10V4zm5 15.3a1.2 1.2 0 1 0 0 2.4 1.2 1.2 0 0 0 0-2.4z"/></svg>
        905-618-3074
      </li>
      <li>
        <svg viewBox="0 0 24 24" aria-hidden="true"><path d="M2 5h20v14H2zm2 2v.4l8 5.2 8-5.2V7zm0 2.8V17h16V9.8l-8 5.2z"/></svg>
        dana@homesbywexley.example
      </li>
      <li>
        <svg viewBox="0 0 24 24" aria-hidden="true"><circle cx="12" cy="12" r="11"/><path d="M7 6c2 1 3 3 2 5s-3 2-3 4l-1 1M15 4c-1 2 0 3 2 3s2 2 1 4-2 3-1 6" stroke="#fff" stroke-width="1.6" fill="none"/></svg>
        www.danawexley.example
      </li>
    </ul>

    <div class="portrait" role="img" aria-label="Photo of the agent in a pinstripe suit holding up a house key"></div>
  </main>
</body>
</html>
```